Billboard design 8x3M RAVU (Spanish company)

We´re located in the south of Spain. We run a local telecom company.
We sell Fiber optic, and mobile phone lines mainly.
The billboard will have to be in Spanish, I would like the price to be something you spot on first sight when passing by in the car.
Our company color is blue, like in our logo which I will add. I will also add a example from what we currently have.
The new offer should be:
1000 megas + 100Gigas movil con llamadas ilimitadas. (meaning 1000Mb fiber optic speed and 100Gb data and unlimited calls for 1 mobile line)
Our details are: phone line 958 47 6620
Website: ra-vu.es

```html
<!DOCTYPE html>
<html lang="es">
<head>
<meta charset="utf-8">
<title>RAVU – Valla 8x3 Fibra + Móvil</title>
<link href="https://fonts.googleapis.com/css2?family=Anton&family=Audiowide&family=Michroma&display=swap" rel="stylesheet">
<style>
  :root{
    --canvas:#e3e3e3;
    --navy:#070b35;
    --navy-mid:#0d1a6e;
    --glow-blue:#1f4fe0;
    --cyan:#37c6ef;
    --gold:#f6b92a;
    --gold-light:#ffe36b;
    --gold-dark:#b9700a;
    --red:#e2293a;
    --red-dark:#a9101f;
    --white:#ffffff;
    --ink:#1d2430;
    --brand-blue:#1b9ad6;
    --icon-dark:#1e3a4f;
  }
  *{margin:0;padding:0;box-sizing:border-box}
  html,body{width:1021px;height:1200px;overflow:hidden;background:var(--canvas)}
  .billboard{
    position:absolute;left:30px;top:420px;width:960px;height:360px;
    box-shadow:0 14px 22px rgba(0,0,0,.35);
    overflow:hidden;
  }
  .offer-panel{
    position:absolute;left:0;top:0;width:960px;height:292px;
    background:
      radial-gradient(ellipse 260px 170px at 860px 10px, rgba(40,90,255,.75), transparent 70%),
      radial-gradient(ellipse 320px 120px at 820px 270px, rgba(230,50,40,.55), transparent 70%),
      radial-gradient(ellipse 200px 90px at 400px 40px, rgba(30,60,200,.35), transparent 70%),
      linear-gradient(90deg, var(--navy) 0%, #0a1050 55%, var(--navy-mid) 100%);
  }
  .headline{
    position:absolute;left:30px;top:52px;white-space:nowrap;
    font-family:"Michroma",sans-serif;font-size:40px;line-height:1;letter-spacing:-1px;
  }
  .headline .fibra{color:var(--cyan)}
  .headline .plus{color:var(--white);font-size:30px;margin:0 10px}
  .headline .movil{color:var(--gold)}
  .subline{
    position:absolute;right:348px;top:104px;white-space:nowrap;
    font-family:"Michroma",sans-serif;font-size:24px;line-height:1;color:var(--white);letter-spacing:-.5px;
  }
  .price{
    position:absolute;left:36px;top:118px;
    font-family:"Anton",sans-serif;font-size:150px;line-height:1;letter-spacing:-2px;
    background:linear-gradient(180deg,var(--gold-light) 0%,var(--gold) 45%,var(--gold-dark) 100%);
    -webkit-background-clip:text;background-clip:text;color:transparent;
    filter:drop-shadow(2px 3px 0 rgba(60,20,0,.6));
  }
  .ribbons{position:absolute;left:240px;top:150px;width:260px;height:110px}
  .ribbon-text{
    position:absolute;left:26px;white-space:nowrap;color:var(--white);
    font-family:"Audiowide",sans-serif;font-style:italic;line-height:1;
    text-shadow:1px 1px 0 rgba(0,0,0,.35);
  }
  .ribbon-text .big{font-size:28px}
  .ribbon-text .small{font-size:14px;margin-left:2px}
  .ribbon-text.speed{top:12px}
  .ribbon-text.data{top:58px}
  .mobile-tag{position:absolute;left:472px;top:188px;width:150px;height:30px}
  .mobile-tag span{
    position:absolute;left:34px;top:9px;font-family:"Michroma",sans-serif;font-size:11px;color:var(--navy);letter-spacing:.5px
  }
  .calls{
    position:absolute;left:510px;top:222px;font-family:"Audiowide",sans-serif;font-style:italic;font-size:16px;line-height:1
  }
  .calls .line1{color:var(--gold)}
  .calls .line2{color:var(--cyan)}
  .hero-art{
    position:absolute;left:640px;top:40px;width:310px;height:232px;border-radius:10px;
    background:
      radial-gradient(ellipse 90px 70px at 210px 70px, rgba(235,240,255,.85), transparent 70%),
      radial-gradient(ellipse 120px 60px at 120px 150px, rgba(120,100,255,.8), transparent 70%),
      radial-gradient(ellipse 170px 60px at 170px 215px, rgba(240,70,50,.55), transparent 75%);
  }
  .contact-band{
    position:absolute;left:0;top:292px;width:960px;height:68px;background:var(--white);
  }
  .contact-item{
    position:absolute;top:18px;display:flex;align-items:center;gap:8px;white-space:nowrap;
    font-family:"Audiowide",sans-serif;font-style:italic;font-size:27px;color:var(--ink);line-height:1;
  }
  .contact-item.phone{left:68px}
  .contact-item.web{left:392px}
  .separator{position:absolute;left:378px;top:22px;width:2px;height:24px;background:var(--ink)}
  .brand-name{
    position:absolute;left:790px;top:16px;font-family:"Audiowide",sans-serif;font-size:32px;color:var(--brand-blue);line-height:1;letter-spacing:2px
  }
</style>
</head>
<body>
  <main class="billboard">
    <section class="offer-panel">
      <h1 class="headline"><span class="fibra">TU FIBRA</span><span class="plus">+</span><span class="movil">MOVIL</span></h1>
      <p class="subline">AL MEJOR PRECIO</p>
      <p class="price">35€</p>

      <div class="ribbons">
        <svg width="260" height="110" viewBox="0 0 260 110">
          <defs>
            <linearGradient id="orangeFill" x1="0" y1="0" x2="0" y2="1">
              <stop offset="0" stop-color="#ffcf4a"/><stop offset="1" stop-color="#e8891a"/>
            </linearGradient>
            <linearGradient id="redFill" x1="0" y1="0" x2="0" y2="1">
              <stop offset="0" stop-color="#f1414f"/><stop offset="1" stop-color="#b6121f"/>
            </linearGradient>
          </defs>
          <polygon points="4,6 246,6 258,24 246,42 4,42" fill="url(#orangeFill)"/>
          <polygon points="4,50 246,50 258,74 246,98 4,98" fill="url(#redFill)"/>
          <circle cx="234" cy="50" r="11" fill="#0a1040" stroke="#ffffff" stroke-width="2"/>
          <path d="M234 44v12M228 50h12" stroke="#ffffff" stroke-width="3"/>
        </svg>
        <p class="ribbon-text speed"><span class="big">1000</span><span class="small">Megas</span></p>
        <p class="ribbon-text data"><span class="big">100</span><span class="small">GIGAS</span></p>
      </div>

      <div class="mobile-tag">
        <svg width="150" height="30" viewBox="0 0 150 30">
          <polygon points="18,4 140,4 150,15 140,26 18,26" fill="var(--cyan)"/>
        </svg>
        <span>MOVIL CON</span>
      </div>
      <p class="calls"><span class="line1">Llamadas</span><br><span class="line2">Ilimitadas</span></p>

      <div class="hero-art" role="img" aria-label="Ilustración de un cohete saliendo de la pantalla de un portátil con estelas de luz roja"></div>
    </section>

    <footer class="contact-band">
      <p class="contact-item phone">
        <svg width="30" height="30" viewBox="0 0 30 30"><circle cx="15" cy="15" r="15" fill="var(--icon-dark)"/><path d="M10 8l3 0 1.5 4-2 1.5a9 9 0 0 0 4 4l1.5-2 4 1.5v3a2 2 0 0 1-2 2A13 13 0 0 1 8 10a2 2 0 0 1 2-2z" fill="#fff"/></svg>
        958 47 6620
      </p>
      <span class="separator"></span>
      <p class="contact-item web">
        <svg width="30" height="30" viewBox="0 0 30 30"><circle cx="15" cy="15" r="15" fill="var(--icon-dark)"/><circle cx="15" cy="15" r="8" fill="none" stroke="#fff" stroke-width="1.6"/><ellipse cx="15" cy="15" rx="3.5" ry="8" fill="none" stroke="#fff" stroke-width="1.4"/><path d="M7 15h16" stroke="#fff" stroke-width="1.4"/></svg>
        WWW.RA-VU.ES
      </p>
      <p class="brand-name">RAVU</p>
    </footer>
  </main>
</body>
</html>
```